New Business Card Design Project

Use the flyer uploaded and website www.brightoakbuilders.com for inspiration.
List Our Services on Backside of business cards
Marcus Delling
Harborline Builders Inc.
Licensed General Contractors
858-471-6093

Contact Information for Business Card

Use the flyer uploaded and website www.brightoakbuilders.com for inspiration. List Our Services on Backside of business cards Marcus Delling Harborline Builders Inc. Licensed General Contractors 858-471-6093

```html
<!DOCTYPE html>
<html lang="en">
<head>
<meta charset="utf-8">
<title>Harborline Builders – Business Card</title>
<link href="https://fonts.googleapis.com/css2?family=Cinzel:wght@400;500;600&display=swap" rel="stylesheet">
<style>
  :root{
    --navy:#0f1c4a;
    --red:#c81f26;
    --red-dark:#a51b21;
    --white:#ffffff;
    --frame:#c9ccd6;
    --page:#eeeeee;
  }
  *{margin:0;padding:0;box-sizing:border-box}
  html,body{width:1200px;height:1200px;overflow:hidden;background:var(--page)}
  body{font-family:"Cinzel",serif;color:var(--white);position:relative}

  .card{position:absolute;left:120px;width:960px;height:548px;background:var(--navy);overflow:hidden}
  .card--front{top:36px}
  .card--back{top:616px}
  .abs{position:absolute}

  /* front */
  .band-top{top:0;left:0}
  .company-line{top:0;left:330px;width:630px;height:75px;display:flex;align-items:center;justify-content:center;font-size:19px;font-weight:600;letter-spacing:.8px}
  .timeline{left:99px;top:75px;width:3px;height:300px;background:var(--red)}
  .icon{width:56px;height:56px}
  .icon--person{left:72px;top:157px}
  .icon--phone{left:76px;top:258px;width:48px;height:48px}
  .icon--pin{left:76px;top:348px;width:48px;height:48px}
  .person-name{left:147px;top:156px;font-size:30px;font-weight:500;font-variant:small-caps;letter-spacing:.5px}
  .person-title{left:148px;top:197px;font-size:18px;font-variant:small-caps}
  .phone{left:148px;top:266px;font-size:22px;font-weight:500}
  .address{left:148px;top:342px;font-size:22px;font-weight:500;font-variant:small-caps;line-height:34px}
  .divider{left:557px;top:168px;width:2px;height:238px;background:var(--white)}
  .brand{display:flex;align-items:center;gap:10px;font-size:24px;font-weight:500;letter-spacing:1px;color:var(--white)}
  .brand__square{width:12px;height:12px;background:var(--red)}
  .brand--front{left:580px;top:275px;width:360px;justify-content:center}
  .band-bottom{left:0;top:493px}
  .licence{left:95px;top:493px;height:55px;display:flex;align-items:center;font-size:20px;font-weight:600;letter-spacing:.5px}

  /* back */
  .web-tab{left:168px;top:0;width:600px;height:46px;background:var(--red);display:flex;align-items:center;justify-content:center;font-size:20px;letter-spacing:2px}
  .brand-frame{left:295px;top:106px;width:352px;height:210px;border:1.5px solid var(--frame);display:flex;align-items:center;justify-content:center}
  .services{left:0;top:362px;width:960px;text-align:center;font-size:16.5px;line-height:43px;letter-spacing:.2px}
  .services .sep{color:var(--red);margin:0 6px}
  .band-foot{left:0;top:515px;width:960px;height:33px;background:var(--red)}
  .band-foot__end{top:0;width:170px;height:33px;background:var(--red-dark)}
  .band-foot__end--left{left:0}
  .band-foot__end--right{right:0;width:180px}
</style>
</head>
<body>

<!-- front side -->
<section class="card card--front" aria-label="Business card front">
  <svg class="abs band-top" width="960" height="75" viewBox="0 0 960 75" aria-hidden="true">
    <polygon points="0,0 300,0 275,75 0,75" fill="var(--red-dark)"/>
    <polygon points="322,0 960,0 960,75 296,75" fill="var(--red)"/>
  </svg>
  <div class="abs company-line">MARCUS DELLING HARBORLINE BUILDERS INC.</div>

  <div class="abs timeline"></div>

  <svg class="abs icon icon--person" viewBox="0 0 56 56" aria-hidden="true">
    <rect x="10" y="10" width="36" height="36" rx="5" transform="rotate(45 28 28)" fill="var(--red)" stroke="var(--white)" stroke-width="3"/>
    <circle cx="28" cy="23" r="4.5" fill="var(--white)"/>
    <path d="M19.5 35 a8.5 7 0 0 1 17 0 z" fill="var(--white)"/>
  </svg>
  <svg class="abs icon icon--phone" viewBox="0 0 48 48" aria-hidden="true">
    <rect x="9" y="9" width="30" height="30" rx="4" transform="rotate(45 24 24)" fill="var(--red)" stroke="var(--white)" stroke-width="3"/>
    <path d="M18 17 l4 -1 2 5 -2.5 1.5 a10 10 0 0 0 5 5 l1.5 -2.5 5 2 -1 4 c-8 1 -15 -6 -14 -14z" fill="var(--white)"/>
  </svg>
  <svg class="abs icon icon--pin" viewBox="0 0 48 48" aria-hidden="true">
    <rect x="9" y="9" width="30" height="30" rx="4" transform="rotate(45 24 24)" fill="var(--red)" stroke="var(--white)" stroke-width="3"/>
    <path d="M24 15 a7 7 0 0 1 7 7 c0 5 -7 12 -7 12 s-7 -7 -7 -12 a7 7 0 0 1 7 -7z" fill="var(--white)"/>
    <circle cx="24" cy="22" r="2.6" fill="var(--red)"/>
  </svg>

  <div class="abs person-name">Marcus Delling</div>
  <div class="abs person-title">Manager</div>
  <div class="abs phone">858-471-6093</div>
  <div class="abs address">2150 Mesa Crest Dr #210,<br>San Diego, CA 92110,<br>United States</div>

  <div class="abs divider"></div>

  <div class="abs brand brand--front"><span class="brand__square"></span>HARBORLINE BUILDERS</div>

  <svg class="abs band-bottom" width="960" height="55" viewBox="0 0 960 55" aria-hidden="true">
    <polygon points="0,0 570,0 592,55 0,55" fill="var(--red)"/>
    <polygon points="588,0 960,0 960,55 612,55" fill="var(--red-dark)"/>
  </svg>
  <div class="abs licence">LICENSED GENERAL CONTRACTORS</div>
</section>

<!-- back side -->
<section class="card card--back" aria-label="Business card back">
  <div class="abs web-tab">WWW.HARBORLINEBUILDERS.COM</div>

  <div class="abs brand-frame">
    <div class="brand"><span class="brand__square"></span>HARBORLINE BUILDERS</div>
  </div>

  <div class="abs services">
    <p>KITCHEN &amp; BATHROOM REMODELING <span class="sep">|</span> PAINTING <span class="sep">|</span> FLOORING <span class="sep">|</span> WINDOW &amp; DOOR REPLACEMENT</p>
    <p>ENERGY EFFICIENT UPGRADES <span class="sep">|</span> PLUMBING <span class="sep">|</span> CUSTOM RENOVATIONS <span class="sep">|</span> WATER &amp; MOULD DAMAGE</p>
    <p>DECK &amp; PATIO CONSTRUCTION <span class="sep">|</span> GARAGE RENOVATION</p>
  </div>

  <div class="abs band-foot">
    <div class="abs band-foot__end band-foot__end--left"></div>
    <div class="abs band-foot__end band-foot__end--right"></div>
  </div>
</section>

</body>
</html>
```